Robotic Physical Therapy office needs a Grand Opening Flyer

We need a Grand Opening flyer design for a robotic physical therapy office named Kinetic Harbor Wellness. We would like it to have a clean, classy, upscale feeling that gives potential clients a V.I.P. feeling. We would like to use the colors black, gray, and yellow (logo will be uploaded).

Event: Thursday, June 1st, 2023 from 12pm-6pm
location: 58274 Pellham Ave, Alderbrook Vale, MN 48519

Industry/Entity Type

Physical therapy

Font styles to use
Script

Colors

Designer to choose colors to be used in the design.

Requirements
Nice to have
• More of a vip feel for the invite

```html
<!DOCTYPE html>
<html lang="en">
<head>
<meta charset="utf-8">
<title>Kinetic Harbor Wellness — Grand Opening Flyer</title>
<link rel="stylesheet" href="https://fonts.googleapis.com/css2?family=Anton&family=Montserrat:wght@400;500;600;800&family=Sacramento&display=swap">
<style>
  :root {
    --page: #e6e6ea;
    --night: #23232f;
    --night-deep: #1b1b26;
    --haze: #2e2e3d;
    --gold: #f7dd1f;
    --white: #ffffff;
    --slate: #6c6c80;
    --slate-edge: #15151d;
    --steel: #5b6a86;
  }
  html, body {
    margin: 0;
    width: 1200px;
    height: 2400px;
    overflow: hidden;
    background: var(--page);
  }
  .flyer {
    position: absolute;
    left: 0;
    top: 351px;
    width: 1200px;
    height: 1697px;
  }
  .flyer-photo {
    position: absolute;
    inset: 0;
    background:
      radial-gradient(ellipse at 55% 40%, var(--haze) 0%, transparent 60%),
      linear-gradient(180deg, var(--night) 0%, var(--night) 55%, var(--night-deep) 100%);
  }
  .flyer-art {
    position: absolute;
    inset: 0;
  }
  .brand-name { font-family: "Montserrat", sans-serif; font-weight: 600; fill: var(--gold); }
  .script-grand { font-family: "Sacramento", cursive; fill: var(--gold); }
  .headline-opening { font-family: "Anton", sans-serif; fill: var(--slate); stroke: var(--slate-edge); stroke-width: 6; paint-order: stroke; }
  .name-primary { font-family: "Montserrat", sans-serif; font-weight: 800; fill: var(--gold); }
  .name-secondary { font-family: "Montserrat", sans-serif; font-weight: 400; fill: var(--white); }
  .event-date { font-family: "Montserrat", sans-serif; font-weight: 400; fill: var(--white); }
  .event-meta { font-family: "Montserrat", sans-serif; font-weight: 500; fill: var(--white); }
  .venue-label { font-family: "Montserrat", sans-serif; font-weight: 500; fill: var(--gold); letter-spacing: 6px; }
  .venue-address { font-family: "Montserrat", sans-serif; font-weight: 400; fill: var(--white); letter-spacing: 1.5px; }
  .site-url { font-family: "Montserrat", sans-serif; font-weight: 500; fill: var(--white); }
  .site-url .site-name { fill: var(--gold); }
  .frame-dash { fill: none; stroke: var(--gold); stroke-width: 4; stroke-dasharray: 20 11; }
  .icon-line { fill: none; stroke: var(--gold); stroke-width: 3; }
</style>
</head>
<body>
<section class="flyer">
  <div class="flyer-photo" role="img" aria-label="Dimmed photo of a therapist guiding a patient through a session in a clinic"></div>

  <svg class="flyer-art" viewBox="0 0 1200 1697" width="1200" height="1697">
    <defs>
      <linearGradient id="gold-rule" x1="0" x2="1" y1="0" y2="0">
        <stop offset="0" stop-color="#f7dd1f" stop-opacity="0"/>
        <stop offset="0.5" stop-color="#f7dd1f"/>
        <stop offset="1" stop-color="#f7dd1f" stop-opacity="0"/>
      </linearGradient>
    </defs>

    <g class="brand">
      <circle cx="452" cy="150" r="62" fill="none" stroke="#f7dd1f" stroke-width="6"/>
      <text class="brand-name" x="532" y="140" font-size="46" textLength="308" lengthAdjust="spacingAndGlyphs">KINETIC HARBOR</text>
      <text class="brand-name" x="532" y="196" font-size="46" textLength="200" lengthAdjust="spacingAndGlyphs">WELLNESS</text>
    </g>

    <path class="frame-dash" d="M312 389 H134 V768 H1068 V470"/>
    <path class="frame-dash" d="M874 389 H1000"/>

    <g class="scissors" transform="translate(1010 372)">
      <path d="M0 0 L62 62" stroke="#f7dd1f" stroke-width="6" stroke-linecap="round"/>
      <path d="M40 8 L40 70" stroke="#f7dd1f" stroke-width="6" stroke-linecap="round"/>
      <circle cx="40" cy="82" r="11" class="icon-line" stroke-width="5"/>
      <circle cx="72" cy="72" r="11" class="icon-line" stroke-width="5"/>
    </g>

    <text class="headline-opening" x="191" y="722" font-size="320" textLength="825" lengthAdjust="spacingAndGlyphs">OPENING</text>
    <text class="script-grand" x="600" y="480" font-size="250" text-anchor="middle">Grand</text>

    <text class="name-primary" x="203" y="951" font-size="118" textLength="800" lengthAdjust="spacing">KINETIC</text>
    <text class="name-secondary" x="197" y="1023" font-size="54" textLength="812" lengthAdjust="spacing">HARBOR WELLNESS</text>

    <rect x="99" y="1069" width="1011" height="3" fill="url(#gold-rule)"/>
    <text class="event-date" x="300" y="1135" font-size="46" textLength="614" lengthAdjust="spacing">JUNE 1ST, 2023</text>
    <rect x="99" y="1157" width="1011" height="3" fill="url(#gold-rule)"/>

    <g class="icon-calendar" transform="translate(294 1212)">
      <rect x="1" y="4" width="34" height="36" class="icon-line"/>
      <line x1="1" y1="14" x2="35" y2="14" class="icon-line"/>
      <line x1="9" y1="0" x2="9" y2="8" class="icon-line"/>
      <line x1="27" y1="0" x2="27" y2="8" class="icon-line"/>
      <path d="M7 20h5M15 20h5M23 20h5M7 27h5M15 27h5M23 27h5M7 34h5M15 34h5" class="icon-line" stroke-width="3"/>
    </g>
    <text class="event-meta" x="341" y="1250" font-size="34" textLength="220" lengthAdjust="spacing">THURSDAY</text>

    <g class="icon-clock" transform="translate(639 1232)">
      <circle r="18" class="icon-line"/>
      <circle r="12" class="icon-line" stroke-width="2"/>
      <path d="M0 -8 V0 L6 4" class="icon-line" stroke-width="2.5"/>
    </g>
    <text class="event-meta" x="671" y="1250" font-size="34" textLength="210" lengthAdjust="spacing">12PM-6PM</text>

    <text class="venue-label" x="600" y="1352" font-size="28" text-anchor="middle">VENUE</text>
    <text class="venue-address" x="600" y="1391" font-size="29" text-anchor="middle">58274 Pellham Ave,</text>
    <text class="venue-address" x="600" y="1428" font-size="29" text-anchor="middle">Alderbrook Vale, MN 48519</text>

    <rect x="534" y="1481" width="80" height="5" rx="2" fill="#5b6a86"/>

    <text class="site-url" x="600" y="1586" font-size="31" text-anchor="middle" textLength="760" lengthAdjust="spacing">www.<tspan class="site-name">KineticHarborWellness</tspan>.com</text>
  </svg>
</section>
</body>
</html>
```